DANCE STUDIO RECITAL FLYER DESIGN 2022

I am looking for a flyer for a dance recital that encapsulates the theme of the flyer. The rhetorical answer to "Where the River Bends Home..." is Hold Me Near but I would like this to be inferred in the design of the flyer. I am looking for something uplifting and positive through the design...I don't know what I am looking for but it needs to be vibrant, heartwarming, and emotional...maybe the world can be dipped in a heart or something with butterflies???

Here are the details...

Brightwing Dance Studio presents
Our 11th Annual Recital, "Where The River Bends Home..."
Saturday, June 25, at 4 pm
Kestrel Ridge High School 31857 Marlow Road
Larkmere Falls, WL 48291

```html
<!DOCTYPE html>
<html lang="en">
<head>
<meta charset="utf-8">
<title>Brightwing Dance Studio – 11th Annual Recital</title>
<link href="https://fonts.googleapis.com/css2?family=Kaushan+Script&family=Oswald:wght@500;600&family=Montserrat:wght@500;700;800&display=swap" rel="stylesheet">
<style>
  :root {
    --backdrop: #eeeeee;
    --paper: #ffffff;
    --orange: #f08a1c;
    --gold: #ffc93c;
    --brand-red: #c62a2a;
    --pink: #e23a84;
    --plum: #3a1d57;
    --ink: #2a2a33;
    --sun: #ffd43b;
    --berry: #c2185b;
    --ring: #e3e3e6;
    --photo-a: #c7332f;
    --photo-b: #f3d6d0;
  }
  * { box-sizing: border-box; margin: 0; padding: 0; }
  html, body { width: 691px; height: 1200px; overflow: hidden; }
  body { background: var(--backdrop); font-family: "Montserrat", sans-serif; position: relative; }

  .flyer {
    position: absolute; left: 26px; top: 180px;
    width: 640px; height: 840px;
    background: var(--paper);
    box-shadow: 0 2px 10px rgba(0,0,0,.12);
    overflow: hidden;
  }
  .top-arc { position: absolute; left: 150px; top: 0; width: 340px; height: 60px; z-index: 1; }
  .hero {
    position: absolute; left: 105px; top: 34px; width: 430px; height: 430px;
    border-radius: 50%; border: 8px solid var(--ring);
    background: radial-gradient(circle at 50% 55%, var(--photo-a) 0%, #a82626 45%, var(--photo-b) 80%);
  }
  .brand {
    position: absolute; top: 70px; left: 0; right: 0; z-index: 3;
    text-align: center; font-weight: 800; font-size: 20px; letter-spacing: 1px;
    color: var(--paper);
  }
  .inset {
    position: absolute; width: 118px; height: 118px; border-radius: 50%;
    border: 6px solid var(--paper); box-shadow: 0 0 0 2px var(--ring);
  }
  .inset.left { left: 70px; top: 330px; background: linear-gradient(160deg, #d94a5a, #f1c7c4); }
  .inset.right-top { left: 470px; top: 255px; background: linear-gradient(160deg, #e6e0e8, #b9a9c2); }
  .inset.right-low { left: 455px; top: 365px; background: linear-gradient(160deg, #f2d0d6, #c8424c); }

  .presents {
    position: absolute; top: 478px; left: 0; right: 0; text-align: center;
    font-weight: 700; font-size: 16px; letter-spacing: 1px; color: var(--ink);
  }
  .butterflies {
    position: absolute; left: 30px; top: 555px; width: 46px; height: 40px;
    border-radius: 40% 60% 50% 50%;
    background: linear-gradient(135deg, #f7b6d2, #e23a84);
    opacity: .6;
  }
  .recital {
    position: absolute; top: 505px; left: 0; right: 0; text-align: center;
    font-family: "Kaushan Script", cursive; font-weight: 400; font-size: 50px;
    color: var(--pink); line-height: 1.1; white-space: nowrap;
  }
  .theme {
    position: absolute; top: 572px; left: 0; right: 0; text-align: center;
    font-family: "Oswald", sans-serif; font-weight: 600; font-size: 36px;
    color: var(--plum); letter-spacing: .5px; white-space: nowrap;
  }
  .theme-rule { position: absolute; top: 628px; left: 120px; width: 400px; height: 2px; background: var(--plum); opacity: .5; }

  .when { position: absolute; top: 652px; left: 0; right: 0; display: flex; justify-content: center; gap: 14px; }
  .when .date {
    background: var(--sun); color: var(--plum); font-weight: 800; font-size: 22px;
    padding: 12px 22px; letter-spacing: .5px; white-space: nowrap;
  }
  .when .time {
    border: 3px solid var(--plum); color: var(--plum); font-weight: 800; font-size: 22px;
    padding: 9px 20px; white-space: nowrap;
  }

  .details { position: absolute; top: 752px; left: 36px; right: 36px; display: flex; justify-content: space-between; align-items: center; gap: 16px; }
  .venue { display: flex; align-items: center; gap: 8px; font-size: 12px; font-weight: 500; color: var(--ink); line-height: 1.45; white-space: nowrap; }
  .web {
    display: flex; align-items: center; gap: 8px; white-space: nowrap;
    background: var(--berry); color: #fff; font-weight: 700; font-size: 14px;
    padding: 10px 16px;
  }
  .bottom-band { position: absolute; bottom: 0; left: 0; width: 100%; height: 10px; background: linear-gradient(90deg, var(--orange), var(--gold)); }
</style>
</head>
<body>
  <main class="flyer">
    <div class="hero" role="img" aria-label="Group photo of young dancers in red costumes"></div>
    <svg class="top-arc" viewBox="0 0 340 60" aria-hidden="true">
      <defs>
        <linearGradient id="arcFill" x1="0" x2="1">
          <stop offset="0" stop-color="#f08a1c"/><stop offset="1" stop-color="#ffc93c"/>
        </linearGradient>
      </defs>
      <path d="M0 0 H340 Q170 80 0 0 Z" fill="url(#arcFill)"/>
    </svg>
    <div class="brand">Brightwing</div>
    <div class="inset left" role="img" aria-label="Dancers performing on stage"></div>
    <div class="inset right-top" role="img" aria-label="Dancers in white costumes"></div>
    <div class="inset right-low" role="img" aria-label="Dancers in pink costumes"></div>

    <p class="presents">BRIGHTWING DANCE STUDIO PRESENTS</p>
    <div class="butterflies" role="img" aria-label="Pink butterflies"></div>
    <h1 class="recital">Our 11th Annual Recital</h1>
    <h2 class="theme">WHERE THE RIVER BENDS HOME...</h2>
    <div class="theme-rule"></div>

    <div class="when">
      <span class="date">SATURDAY, JUNE 25</span>
      <span class="time">AT 4 PM</span>
    </div>

    <div class="details">
      <div class="venue">
        <svg width="20" height="28" viewBox="0 0 22 30" aria-hidden="true">
          <path d="M11 0C5 0 0 5 0 11c0 8 11 19 11 19s11-11 11-19C22 5 17 0 11 0z" fill="#c2185b"/>
          <circle cx="11" cy="11" r="4" fill="#fff"/>
        </svg>
        <span>Kestrel Ridge High School 31857 Marlow Road<br>Larkmere Falls, WL 48291</span>
      </div>
      <div class="web">
        <svg width="16" height="16" viewBox="0 0 18 18" aria-hidden="true">
          <circle cx="9" cy="9" r="7.5" fill="none" stroke="#fff" stroke-width="1.5"/>
          <ellipse cx="9" cy="9" rx="3.5" ry="7.5" fill="none" stroke="#fff" stroke-width="1.2"/>
          <line x1="1.5" y1="9" x2="16.5" y2="9" stroke="#fff" stroke-width="1.2"/>
        </svg>
        brightwingdance.com
      </div>
    </div>
    <div class="bottom-band"></div>
  </main>
</body>
</html>
```